CREATE A BUSINESS CARD FOR A BOAT CLEANING SERVICE

WE ARE STARTING A NEW BOAT CLEANING BUSINESS. WE DIVE UNDERWATER TO CLEAN BOAT HULLS, JETTIES, UNDERWATER STRUCTURES ETC. WE ARE LOOKING FOR AN UPPERMARKET MODERN LOGO AND BUSINESS CARD AS ALOT OF OUR TARGET MARKET WILL BE HIGH END. YOU HAVE TO DESIGN A BUSINESS CARD AND LOGO SEPERATELY .
THE BUSINESS CARD DIMESNION MUST BE STANDARD SIZE.
The standard dimensions of a printed business card are 3.5 x 2 inches

Target Market(s)

UNDERWATER SERVICED

Industry/Entity Type

Business

Contact Information for Business Card

HOLLAND UNDERWATER SERVICES

Font styles to use
Serif

Colors

Designer to choose colors to be used in the design.

Requirements
Must have
• HOLLAND
Nice to have
• dark
Should not have
• more than 3 colors

```html
<!DOCTYPE html>
<html lang="en">
<head>
<meta charset="utf-8">
<title>Holland Underwater Service – Business Card</title>
<link rel="stylesheet" href="https://fonts.googleapis.com/css2?family=Montserrat:wght@400;600;700&family=Open+Sans:wght@400;600&display=swap">
<style>
  :root {
    --page: #e9e6e1;
    --card-black: #0b0c0e;
    --blue: #2f8fd6;
    --blue-deep: #1f6fb3;
    --white: #f3f5f7;
    --silver: #cfd4d8;
    --muted: #b9bec4;
  }
  * { margin: 0; padding: 0; box-sizing: border-box; }
  html, body {
    width: 1200px; height: 1023px; overflow: hidden;
    background: var(--page);
  }
  .card {
    position: absolute; left: 355px; top: 82px;
    width: 490px; height: 858px;
    border-radius: 26px; overflow: hidden;
    background: linear-gradient(160deg, #1a1c20 0%, var(--card-black) 55%);
    box-shadow: 0 18px 40px rgba(0,0,0,.28);
    color: var(--white);
    font-family: "Open Sans", Arial, sans-serif;
  }
  .brand { position: absolute; left: 0; right: 0; top: 120px; text-align: center; }
  .brand-name {
    font-family: "Montserrat", Arial, sans-serif; font-weight: 400;
    font-size: 46px; letter-spacing: 22px; color: var(--blue);
    padding-left: 22px;
  }
  .brand-tag {
    font-family: "Montserrat", Arial, sans-serif; font-weight: 400;
    font-size: 17px; letter-spacing: 6.5px; color: var(--white);
    margin-top: 4px; padding-left: 6px;
  }
  .person { position: absolute; left: 52px; top: 300px; }
  .person-name {
    font-family: "Montserrat", Arial, sans-serif; font-weight: 700;
    font-size: 30px; color: var(--blue); letter-spacing: 1px;
  }
  .person-title { font-size: 16px; color: var(--white); margin-top: 2px; }
  .person-rule { width: 26px; height: 2px; background: var(--blue); margin: 14px 0 18px; }
  .contact { list-style: none; font-size: 17px; line-height: 27px; }
  .contact li { display: flex; align-items: center; gap: 10px; }
  .contact .icon { width: 13px; height: 13px; flex: none; }
  .contact .no-icon { width: 13px; flex: none; }
  .contact .web { color: var(--blue); }
  .band { position: absolute; left: 0; bottom: 0; width: 490px; height: 270px; }
  .partner-badge {
    position: absolute; left: 38px; bottom: 150px;
    width: 62px; height: 44px; border-radius: 50%;
    background: rgba(255,255,255,.22);
  }
  .footer-brand {
    position: absolute; left: 150px; bottom: 62px;
    display: flex; align-items: center; gap: 8px;
  }
  .footer-dot { width: 34px; height: 34px; border-radius: 50%; background: var(--white); }
  .footer-text { font-family: "Montserrat", Arial, sans-serif; }
  .footer-name { font-weight: 700; font-size: 30px; color: var(--white); letter-spacing: 1px; line-height: 1; }
  .footer-tag { font-weight: 700; font-size: 8.5px; color: var(--white); letter-spacing: 1.6px; margin-top: 2px; }
</style>
</head>
<body>
  <article class="card">
    <header class="brand">
      <div class="brand-name">HOLLAND</div>
      <div class="brand-tag">UNDERWATER SERVICE</div>
    </header>

    <section class="person">
      <div class="person-name">MARTIN GRAY</div>
      <div class="person-title">President</div>
      <div class="person-rule"></div>
      <ul class="contact">
        <li><span class="no-icon"></span>140, 318- 9th Street, NW</li>
        <li><span class="no-icon"></span>Halton, AB T3K 2P5</li>
        <li>
          <svg class="icon" viewBox="0 0 16 16" aria-hidden="true"><path d="M3 1h3l1.5 4-2 1.3a9 9 0 0 0 4.2 4.2L11 8.5l4 1.5v3c0 1-1 2-2 2A12 12 0 0 1 1 3c0-1 1-2 2-2z" fill="var(--blue)"/></svg>
          (555) 214-0398
        </li>
        <li>
          <svg class="icon" viewBox="0 0 16 16" aria-hidden="true"><rect x="1" y="3" width="14" height="10" rx="1" fill="none" stroke="var(--blue)" stroke-width="1.6"/><path d="M1.5 3.5 8 9l6.5-5.5" fill="none" stroke="var(--blue)" stroke-width="1.6"/></svg>
          info@hollandunderwater.com
        </li>
        <li>
          <svg class="icon" viewBox="0 0 16 16" aria-hidden="true"><circle cx="8" cy="8" r="6.5" fill="none" stroke="var(--blue)" stroke-width="1.6"/><path d="M1.5 8h13M8 1.5c-3 3.5-3 9.5 0 13M8 1.5c3 3.5 3 9.5 0 13" fill="none" stroke="var(--blue)" stroke-width="1.2"/></svg>
          <span class="web">www.hollandunderwater.com</span>
        </li>
      </ul>
    </section>

    <svg class="band" viewBox="0 0 490 270" aria-hidden="true">
      <defs>
        <linearGradient id="bandBlue" x1="0" y1="0" x2="0" y2="1">
          <stop offset="0" stop-color="#3a9be0"/>
          <stop offset="1" stop-color="#1f6fb3"/>
        </linearGradient>
        <linearGradient id="bandSilver" x1="0" y1="0" x2="1" y2="0">
          <stop offset="0" stop-color="#aab1b7"/>
          <stop offset="1" stop-color="#e6e9ec"/>
        </linearGradient>
      </defs>
      <polygon points="0,10 490,62 490,150 330,168 372,118 0,40" fill="url(#bandSilver)"/>
      <polygon points="0,40 372,118 330,168 490,150 490,270 0,270" fill="url(#bandBlue)" stroke="#0b0c0e" stroke-width="5" stroke-linejoin="miter"/>
    </svg>

    <div class="partner-badge"></div>
    <div class="footer-brand">
      <div class="footer-dot"></div>
      <div class="footer-text">
        <div class="footer-name">HOLLAND</div>
        <div class="footer-tag">UNDERWATER SERVICES</div>
      </div>
    </div>
  </article>
</body>
</html>
```